Animation College website

Name of College: Brightloom Academy of 3D Animation and VFX

We need a redesigned modern website for Brightloom. The web-design should communicate a VFX and animation school and education. We will also need full access to the website once completed. We will also need access to the website to be able to make changes to the content and site ideally the website would be built on Wordpress.

To learn more about what the College please visit: http://brightloom-academy.example/
The video on the homepage demonstrates why Brightloom is a unique college offering 3D animation and VFX. The direct link to the video can be watched here: https://videohost.example/482915036

Client Profile Summary: Brightloom is an improved concept in job skills training for the 3D animation and visual effects industries. Our high graduate job placement numbers are based on the assertion that job skills must include more than simply learning to use software tools. Where nearly every digital media program teaches tools, job skills training should be about learning how to do a job in addition to learning how to use software tools. Brightloom is taught in an apprenticeship style with very experienced faculty mentoring and teaching students to learn how to master their craft (VFX and animation) so they can seamlessly step into industry and excel.

Target Market(s)

High school students, students interested in learning about animation and 3D.

Industry/Entity Type

College

Coding

Coded - Design and coding required

Number of Pages Required

5+ page

Font styles to use
Sans Serif

Colors

Designer to choose colors to be used in the design.

Requirements
Must have
• Please include the video on the current Brightloom-academy.example website. https://videohost.example/482915036
• Use the same content on the current brightloom-academy.example website.
• Include a page to showcase student work.
• Website must also be mobile responsive.
Should not have
• The attached PDF of the landing page is just an example of something we like. You do not have to replicate this. The PDF landing page is showing the colour blue you should incorporate.

```html
<!DOCTYPE html>
<html lang="en">
<head>
<meta charset="utf-8">
<title>Brightloom Academy – One-Year Intensive Training Program</title>
<link rel="stylesheet" href="https://fonts.googleapis.com/css2?family=Lato:ital,wght@0,300;0,400;0,700;1,400&display=swap">
<style>
:root{
  --blue:#1f5d9c;
  --blue-deep:#174a80;
  --blue-text:#1f5ea8;
  --ink:#222;
  --body:#444;
  --yellow:#f2c500;
  --panel:#2a2a2a;
  --white:#fff;
  --rule:#e2e2e2;
}
*{margin:0;padding:0;box-sizing:border-box}
html,body{width:1200px;height:4063px;overflow:hidden}
body{font-family:"Lato",Arial,sans-serif;color:var(--body);background:#fff;position:relative}
section,footer{position:absolute;left:0;width:1200px}

/* hero */
.hero{top:0;height:767px;background:#151515}
.hero-photo{position:absolute;inset:0;background:radial-gradient(ellipse at 45% 40%,#5c6470 0%,#34383d 40%,#151515 80%)}
.brand{position:absolute;left:100px;top:28px;display:flex;align-items:center;gap:12px}
.brand-dot{width:44px;height:44px;border-radius:50%;background:var(--blue)}
.brand-name{font-size:34px;font-weight:700;color:var(--white);letter-spacing:1px}
.hero-title{position:absolute;left:84px;top:368px;width:670px;background:rgba(20,20,20,.85);color:#fff;font-size:23px;font-weight:700;padding:9px 14px;white-space:nowrap}
.hero-tag{position:absolute;left:84px;top:414px;background:var(--yellow);color:#222;font-size:17px;padding:7px 14px;white-space:nowrap}
.arrow{position:absolute;width:46px;height:46px;border-radius:50%;display:flex;align-items:center;justify-content:center}
.arrow.left{left:18px;top:370px;background:rgba(0,0,0,.4)}
.arrow.right{left:1126px;top:370px;background:#111}
.form{position:absolute;left:777px;top:176px;width:404px;height:555px;background:var(--panel)}
.form-head{background:#1c1c1c;color:#fff;font-size:27px;padding:14px 30px;border-bottom:1px solid #444}
.form-note{color:#ddd;font-size:15px;font-style:italic;text-align:center;padding:14px 30px 10px;line-height:1.4}
.field{margin:0 0 12px 30px;width:263px;height:38px;background:#fff;border:1px solid #ccc;font-size:13px;color:#555;padding:11px 12px}
.submit{margin:22px 0 0 30px;width:263px;height:54px;background:var(--blue);color:#fff;font-size:21px;text-align:center;line-height:54px}

/* partners */
.partners{top:767px;height:230px;background:var(--blue)}
.badge{position:absolute;background:rgba(255,255,255,.9)}
.badge.circle{border-radius:50%;width:125px;height:125px;top:818px}
.badge.leaf{width:110px;height:80px;top:840px;border-radius:8px}

/* generic text block */
.block h2{font-size:33px;font-weight:700;color:var(--ink);text-align:center}
.block .sub{font-size:20px;font-style:italic;color:var(--blue-text);text-align:center;margin-top:12px;padding-bottom:22px;border-bottom:1px solid var(--rule);width:1000px;margin-left:100px}
.block p{font-size:14.5px;line-height:1.75;text-align:center;width:940px;margin:26px auto 0}

.intro{top:997px;height:379px;padding-top:62px}

/* video */
.video{top:1376px;height:553px;background:radial-gradient(ellipse at 50% 50%,#3f3a36 0%,#1d1b1a 60%,#0c0c0c 100%)}
.player{position:absolute;left:252px;top:73px;width:693px;height:401px;background:linear-gradient(135deg,#6b6f73,#3a3d40 60%,#222)}
.player-bar{position:absolute;left:0;bottom:0;width:100%;height:36px;background:rgba(0,0,0,.6)}
.player-track{position:absolute;left:52px;top:15px;width:560px;height:6px;background:#666}
.player-title{position:absolute;left:440px;top:100px;color:#eee;font-size:30px;font-weight:300}

/* learn */
.learn{top:1929px;height:577px;padding-top:86px}
.learn ol{width:560px;margin:18px 0 0 340px;font-size:14.5px;line-height:1.7}
.learn ol li{margin-bottom:14px}

/* testimonial */
.quote{top:2506px;height:506px;background:radial-gradient(ellipse at 50% 50%,#3d4a5a,#161a20 80%)}
.quote-box{position:absolute;left:293px;top:90px;width:770px;height:377px;background:rgba(31,93,156,.75);border:1px solid rgba(255,255,255,.4)}
.avatar{position:absolute;left:556px;top:50px;width:80px;height:80px;border-radius:50%;background:linear-gradient(#8a7060,#4a3a30);border:3px solid #fff}
.quote-text{position:absolute;left:56px;top:100px;width:500px;color:#fff;font-size:17px;font-style:italic;line-height:1.55}
.qmark{position:absolute;color:rgba(255,255,255,.55);font-size:70px;font-family:Georgia,serif;line-height:1}
.quote-name{position:absolute;right:108px;top:262px;text-align:right;color:#fff;font-size:17px;line-height:1.5}
.quote-name b{display:block}

/* advantage */
.advantage{top:3012px;height:672px;padding-top:70px}
.ticks{list-style:none;margin:28px 0 0 440px;font-size:14.5px}
.ticks li{height:37px;display:flex;align-items:center;gap:10px}

/* cta */
.cta{top:3684px;height:271px;background:var(--blue-deep);text-align:center;color:#fff}
.cta h3{font-size:42px;font-weight:300;margin-top:62px}
.cta p{font-size:26px;margin-top:28px;letter-spacing:.5px}

/* footer */
.footer{top:3955px;height:108px;background:#f4f4f4;font-size:11px;color:#666}
.footer .copy{position:absolute;left:100px;top:48px}
.footer .social{position:absolute;left:750px;top:40px;display:flex;align-items:center;gap:8px}
.dot{width:24px;height:24px;border-radius:50%}
.footer .code{position:absolute;left:1125px;top:48px}
</style>
</head>
<body>

<section class="hero">
  <div class="hero-photo" role="img" aria-label="Student working at a 3D animation workstation in a studio"></div>
  <div class="brand"><span class="brand-dot"></span><span class="brand-name">Brightloom</span></div>
  <div class="hero-title">3D Animation &amp; VFX One-Year Intensive Training Program</div>
  <div class="hero-tag">Train alongside passionate and experienced industry masters</div>
  <div class="arrow left"><svg width="16" height="24"><path d="M12 2 3 12l9 10" stroke="#ccc" stroke-width="3" fill="none"/></svg></div>
  <div class="arrow right"><svg width="16" height="24"><path d="M4 2l9 10-9 10" stroke="#fff" stroke-width="3" fill="none"/></svg></div>
  <form class="form">
    <div class="form-head">WANT TO KNOW MORE?</div>
    <div class="form-note">Complete this form to receive more information about program details &amp; more!</div>
    <div class="field">FIRST NAME*</div>
    <div class="field">LAST NAME*</div>
    <div class="field">PHONE*</div>
    <div class="field">EMAIL*</div>
    <div class="field">COUNTRY OF RESIDENCE*</div>
    <div class="field">COMMENTS</div>
    <div class="submit">SEND ME FREE INFO</div>
  </form>
</section>

<section class="partners">
  <svg style="position:absolute;left:80px;top:100px" width="16" height="28"><path d="M13 2 3 14l10 12" stroke="rgba(255,255,255,.5)" stroke-width="3" fill="none"/></svg>
  <svg style="position:absolute;left:1104px;top:100px" width="16" height="28"><path d="M3 2l10 12-10 12" stroke="rgba(255,255,255,.5)" stroke-width="3" fill="none"/></svg>
</section>
<div class="badge" style="left:138px;top:812px;width:110px;height:135px;border-radius:55px 55px 10px 10px"></div>
<div class="badge circle" style="left:290px"></div>
<div class="badge circle" style="left:485px"></div>
<div class="badge leaf" style="left:730px"></div>
<div class="badge leaf" style="left:965px;width:130px"></div>

<section class="intro block">
  <h2>One-Year Intensive Training Program</h2>
  <div class="sub">An exciting, comprehensive program with a 100% graduate employment rate</div>
  <p>The 48-week Brightloom One-Year Intensive Training Program is designed to provide students the practical skills and real-world experience needed to thrive in the film and TV animation, and VFX industries. Students are mentored by our passionate instructors who have extensive industry experience. Each of our instructors knows exactly what it takes for students to be successful. We carefully crafted the program curriculum to teach students how to function in a real production team so that they can be highly-effective professionals once they enter the workforce.</p>
</section>

<section class="video">
  <div class="player" role="img" aria-label="Video: a graduate talks about why Brightloom is unique">
    <div class="player-title">Phenomenal</div>
    <div class="player-bar"><div class="player-track"></div>
      <svg style="position:absolute;left:18px;top:10px" width="16" height="16"><path d="M2 1l12 7-12 7z" fill="#fff"/></svg>
    </div>
  </div>
</section>

<section class="learn block">
  <h2>Learn Animation &amp; Visual Effects Production from the Experts</h2>
  <div class="sub">The world's first and sole simulated production training program</div>
  <p>Our Philosophy is unique. We don't focus on grades. Instead, we focus on preparing each of our students for the challenges of working as 3D artists such as animators, lighting TDs, riggers, modellers, compositors and more. Our instructors teach you until you're confident in your skills. If you need more help, we train you until you're ready.</p>
  <p style="margin-top:24px">Students grasp valuable skills that employers are looking for over the course of three intensive terms:</p>
  <ol>
    <li>Core Skills: An intensive introduction to skills involving cameras, modeling, animation, dynamics, lighting, composition, production, and more.</li>
    <li>Transition into Practice: Expand on core skills with advanced training and team production</li>
    <li>Practical Training: Practical hands-on production and dailies training</li>
  </ol>
</section>

<section class="quote">
  <div class="quote-box">
    <span class="qmark" style="left:40px;top:50px">“</span>
    <div class="quote-text">I was able to get my 1st job only two weeks after finishing this program. It is the future of VFX training. Brightloom has changed my life and changed the way that I think about the world around me. I would highly recommend this program above any other, to anyone wishing to pursue a career in the film industry.</div>
    <span class="qmark" style="left:555px;top:200px">”</span>
    <div class="quote-name"><b>Dana Whitlow</b>Lighting Artist, Northlight Studio</div>
  </div>
  <div class="avatar" role="img" aria-label="Portrait of the graduate"></div>
</section>

<section class="advantage block">
  <h2>The Brightloom Advantage</h2>
  <div class="sub">A program designed by industry, for industry</div>
  <p>There's a reason why each of our graduates have found work in their field. We don't sell courses, we provide relevant training. In order to bring out the best in our students, we run a program that we know will maximize each student's potential.</p>
  <p style="margin-top:40px">Brightloom offers an un-paralleled training experience. Here are a few examples of what makes our school unique:</p>
  <ul class="ticks">
    <li><svg width="16" height="16"><circle cx="8" cy="8" r="8" fill="#1f5ea8"/><path d="M4 8l3 3 5-6" stroke="#fff" stroke-width="2" fill="none"/></svg>Affordable tuition for both domestic and international students</li>
    <li><svg width="16" height="16"><circle cx="8" cy="8" r="8" fill="#1f5ea8"/><path d="M4 8l3 3 5-6" stroke="#fff" stroke-width="2" fill="none"/></svg>A faculty of 12 world-class industry masters</li>
    <li><svg width="16" height="16"><circle cx="8" cy="8" r="8" fill="#1f5ea8"/><path d="M4 8l3 3 5-6" stroke="#fff" stroke-width="2" fill="none"/></svg>Maximum class size of 12 students</li>
    <li><svg width="16" height="16"><circle cx="8" cy="8" r="8" fill="#1f5ea8"/><path d="M4 8l3 3 5-6" stroke="#fff" stroke-width="2" fill="none"/></svg>One-on-one mentorship</li>
    <li><svg width="16" height="16"><circle cx="8" cy="8" r="8" fill="#1f5ea8"/><path d="M4 8l3 3 5-6" stroke="#fff" stroke-width="2" fill="none"/></svg>Employment opportunities</li>
    <li><svg width="16" height="16"><circle cx="8" cy="8" r="8" fill="#1f5ea8"/><path d="M4 8l3 3 5-6" stroke="#fff" stroke-width="2" fill="none"/></svg>Scholarships</li>
    <li><svg width="16" height="16"><circle cx="8" cy="8" r="8" fill="#1f5ea8"/><path d="M4 8l3 3 5-6" stroke="#fff" stroke-width="2" fill="none"/></svg>And more!</li>
  </ul>
</section>

<section class="cta">
  <h3>Want to learn more?</h3>
  <p>FILL OUT THE FORM ABOVE TO RECEIVE INFORMATION ABOUT THE PROGRAM!</p>
</section>

<footer class="footer">
  <div class="copy">© 2017. Brightloom Academy of 3D Animation &amp; VFX. All rights reserved.</div>
  <div class="social">Connect with our social network:
    <span class="dot" style="background:#1f5d9c;margin-left:12px"></span>
    <span class="dot" style="background:#1f5d9c"></span>
    <span class="dot" style="background:#e39a2b"></span>
    <span class="dot" style="background:#1f5d9c"></span>
    <span class="dot" style="background:#c4302b"></span>
  </div>
  <div class="code">C16</div>
</footer>

</body>
</html>
```